Designer Instructions – Updated Referral Program Flyer

(Based on the mock-up in “Brief Layout and Instructions.pdf”)

OVERALL STYLE + LAYOUT

Maintain the same general layout, structure, and flow as the mock-up flyer (front and back).

This is an update of an older flyer, not a full redesign — keep the same sections, proportions, and overall visual feel, but with cleaner, more modern design improvements.

The final flyer should look clean, bold, professional, and high-impact, geared toward realtors, property managers, and contractors who refer work.

FRONT SIDE INSTRUCTIONS
1. Header Section

Remove the Rebuild Harbor Crest logo from the top banner.
(Shown on page 1 of the PDF)

2. Main Headline

Keep the same three-line structure:
EARN
UNLIMITED
CASH

Center it, maximize impact, and increase the font size of CASH so all three words match in importance.

Make the headline bold, clean, and the main focal point.

3. Cash Incentive Box

Keep the "$500 minimum OR 10% per referral" box, but upgrade the graphics to look sharper and more modern.

Ensure the wording matches exactly what’s in the mock-up.

4. Premier Partner Program Ribbon

Clean up and modernize the "PREMIER PARTNER PROGRAM" bar while keeping the same position and structure.

Ensure the checkmark badge remains crisp and professional.

5. Supporting Icons Section

Keep the four icons/benefit boxes (Guaranteed Payout, Free Evaluations, Affordable Solutions, Industry Leaders) in the same order.

Update the icons to cleaner, more modern styles — but maintain the same meanings.

Improve alignment and spacing for sharper visual consistency.

6. Remove Icons in Contact Area

At the bottom (“CALL TEXT OR BOOK ONLINE 858-471-6093 BrightlaneRenovate.com”), remove the phone and internet icons, as noted on page 2 of the PDF.

7. Replace All Images

I (Dorian) will provide all updated stock images separately via email.

Replace the flood/water-damage imagery and roof leak with the new images I send.

Keep image placement and proportions the same as the mock-up.

BACK SIDE INSTRUCTIONS
1. Header Image + “REFER / EARN” Section

Maintain the same large split-image layout (“The more you refer, the more you earn”).

Replace all background imagery with the new assets I will send.

Keep the CASH FLOW image section but modernize the type and spacing.

2. “HOW IT WORKS” Section

Preserve the three-column layout:

Refer Flood, Water & Mold Damage

We Take Care of Everything (evaluations/insurance)

Get Paid to Share

Update images, tighten spacing, and use modern iconography.

3. Remove Phone/Internet Icons

Same as the front side — remove small communication icons and keep only the text/number/URL.

4. Bottom Contact Bar

Keep the blue bar, same wording, same layout — just modernize the style if needed for clarity.

5. Replace All Back-Side Images

Again, I will email you the image assets.

Keep the layout EXACT — just update with higher-quality photos and improved design.

TEXT CONTENT (Keep as-is unless spacing adjustments needed)

All text shown in the PDF should remain exactly the same unless spacing or visual balance requires minor adjustments.
Example from page 3:

“REFER FLOOD, MOLD & CONSTRUCTION JOBS”

“We Schedule a Free Estimate. If Approved, You Get Paid.”

“Everybody Benefits From Referrals”

Everything stays, just refreshed and visually improved.

DESIGN GOALS

Flyer should look high-end and trustworthy, not salesy.

Consistent color theme: blues, whites, yellows, same palette as original.

Use bold, modern fonts with strong readability.

Ensure all headlines pop and all benefit boxes are clean, well-aligned, and evenly spaced.

The final result should feel like a premium referral program flyer for a top-tier restoration/remodel company.

FILES I WILL PROVIDE

I will send the designer:

All replacement stock photos

Any updated logos (if needed)

Original high-resolution version of the mock-up (if available)

Any additional icons preferred

Colors
0054AA
0677BA
7BADD7
CADEEF
E8F1F8

Requirements
Must have
• Designer Instructions – Updated Referral Program Flyer (Based on the mock-up in “Brief Layout and Instructions.pdf”) OVERALL STYLE + LAYOUT Maintain the same general layout, structure, and flow as the mock-up flyer (front and back). This is an update of an older flyer, not a full redesign — keep the same sections, proportions, and overall visual feel, but with cleaner, more modern design improvements. The final flyer should look clean, bold, professional, and high-impact, geared toward realtors, property managers, and contractors who refer work. FRONT SIDE INSTRUCTIONS 1. Header Section Remove the Rebuild Harbor Crest logo from the top banner. (Shown on page 1 of the PDF) 2. Main Headline Keep the same three-line structure: EARN UNLIMITED CASH Center it, maximize impact, and increase the font size of CASH so all three words match in importance. Make the headline bold, clean, and the main focal point. 3. Cash Incentive Box Keep the "$500 minimum OR 10% per referral" box, but upgrade the graphics to look sharper and more modern. Ensure the wording matches exactly what’s in the mock-up. 4. Premier Partner Program Ribbon Clean up and modernize the "PREMIER PARTNER PROGRAM" bar while keeping the same position and structure. Ensure the checkmark badge remains crisp and professional. 5. Supporting Icons Section Keep the four icons/benefit boxes (Guaranteed Payout, Free Evaluations, Affordable Solutions, Industry Leaders) in the same order. Update the icons to cleaner, more modern styles — but maintain the same meanings. Improve alignment and spacing for sharper visual consistency. 6. Remove Icons in Contact Area At the bottom (“CALL TEXT OR BOOK ONLINE 858-471-6093 BrightlaneRenovate.com”), remove the phone and internet icons, as noted on page 2 of the PDF. 7. Replace All Images I (Dorian) will provide all updated stock images separately via email. Replace the flood/water-damage imagery and roof leak with the new images I send. Keep image placement and proportions the same as the mock-up. BACK SIDE INSTRUCTIONS 1. Header Image + “REFER / EARN” Section Maintain the same large split-image layout (“The more you refer, the more you earn”). Replace all background imagery with the new assets I will send. Keep the CASH FLOW image section but modernize the type and spacing. 2. “HOW IT WORKS” Section Preserve the three-column layout: Refer Flood, Water & Mold Damage We Take Care of Everything (evaluations/insurance) Get Paid to Share Update images, tighten spacing, and use modern iconography. 3. Remove Phone/Internet Icons Same as the front side — remove small communication icons and keep only the text/number/URL. 4. Bottom Contact Bar Keep the blue bar, same wording, same layout — just modernize the style if needed for clarity. 5. Replace All Back-Side Images Again, I will email you the image assets. Keep the layout EXACT — just update with higher-quality photos and improved design. TEXT CONTENT (Keep as-is unless spacing adjustments needed) All text shown in the PDF should remain exactly the same unless spacing or visual balance requires minor adjustments. Example from page 3: “REFER FLOOD, MOLD & CONSTRUCTION JOBS” “We Schedule a Free Estimate. If Approved, You Get Paid.” “Everybody Benefits From Referrals” Everything stays, just refreshed and visually improved. DESIGN GOALS Flyer should look high-end and trustworthy, not salesy. Consistent color theme: blues, whites, yellows, same palette as original. Use bold, modern fonts with strong readability. Ensure all headlines pop and all benefit boxes are clean, well-aligned, and evenly spaced. The final result should feel like a premium referral program flyer for a top-tier restoration/remodel company. FILES I WILL PROVIDE I will send the designer: All replacement stock photos Any updated logos (if needed) Original high-resolution version of the mock-up (if available) Any additional icons preferred

```html
<!DOCTYPE html>
<html lang="en">
<head>
<meta charset="utf-8">
<title>Referral Program Flyer – Front and Back</title>
<link rel="stylesheet" href="https://fonts.googleapis.com/css2?family=Anton&family=Roboto+Condensed:wght@400;700;900&display=swap">
<style>
  :root {
    --navy: #0b2f63;
    --blue: #0054AA;
    --blue-mid: #0677BA;
    --blue-soft: #7BADD7;
    --blue-pale: #CADEEF;
    --blue-mist: #E8F1F8;
    --yellow: #F7C600;
    --red: #D3202F;
    --white: #ffffff;
    --ink: #1d2a3a;
    --head: "Anton", Impact, sans-serif;
    --body: "Roboto Condensed", Arial, sans-serif;
  }
  * { box-sizing: border-box; margin: 0; padding: 0; }
  html, body { width: 900px; height: 1200px; overflow: hidden; background: var(--white); }
  body { position: relative; font-family: var(--body); color: var(--ink); }

  .card { position: absolute; left: 25px; width: 850px; background: var(--white); overflow: hidden; box-shadow: 0 2px 8px rgba(0,0,0,.18); }
  .card--front { top: 20px; height: 480px; }
  .card--back { top: 600px; height: 540px; }
  .abs { position: absolute; }

  /* ---------- FRONT ---------- */
  .hero-photo { left: 300px; top: 0; width: 550px; height: 192px;
    background: linear-gradient(135deg, #b89a7a 0%, #8d6d52 45%, #2f7fc0 70%, #1c5a94 100%);
    clip-path: polygon(12% 0, 100% 0, 100% 100%, 0 100%); }
  .hero-panel { left: 0; top: 0; width: 400px; height: 192px; background: var(--navy);
    clip-path: polygon(0 0, 100% 0, 87% 100%, 0 100%); }
  .headline { left: 0; top: 8px; width: 350px; text-align: center; font-family: var(--head); line-height: .95; text-transform: uppercase; }
  .headline .line { display: block; }
  .headline .earn { color: var(--yellow); font-size: 46px; }
  .headline .unlimited { color: var(--white); font-size: 40px; letter-spacing: 1px; }
  .headline .cash { color: var(--yellow); font-size: 52px; }
  .hero-tag { left: 22px; top: 152px; width: 318px; height: 32px; background: var(--yellow); color: var(--navy);
    font-family: var(--head); font-size: 21px; line-height: 32px; text-align: center; letter-spacing: .5px; }

  .offer { left: 30px; top: 204px; width: 330px; height: 52px; display: flex; align-items: center; gap: 10px; }
  .offer-chip { background: var(--red); color: var(--white); height: 48px; padding: 0 12px; display: flex; align-items: center; gap: 6px; border-radius: 6px; }
  .offer-chip strong { font-family: var(--head); font-size: 30px; font-weight: 400; }
  .offer-chip span { font-weight: 900; font-size: 12px; line-height: 1.05; text-transform: uppercase; }
  .offer-or { width: 40px; height: 40px; border-radius: 50%; border: 3px solid var(--navy); color: var(--navy);
    font-family: var(--head); font-size: 17px; display: flex; align-items: center; justify-content: center; }

  .premier { left: 430px; top: 196px; width: 400px; height: 64px; }
  .premier-label { position: absolute; left: 182px; top: 0; background: var(--navy); color: var(--white);
    font-size: 10px; font-weight: 900; letter-spacing: 1px; padding: 2px 10px; }
  .premier-pill { position: absolute; top: 18px; height: 40px; font-family: var(--head); font-size: 24px; line-height: 40px; letter-spacing: 1px; }
  .premier-pill--partner { left: 20px; width: 160px; background: var(--red); color: var(--white); text-align: center; border-radius: 20px 0 0 20px; }
  .premier-pill--program { left: 222px; width: 170px; background: var(--blue-pale); color: var(--navy); text-align: center; border-radius: 0 20px 20px 0; }
  .premier-badge { position: absolute; left: 170px; top: 10px; width: 58px; height: 58px; }

  .wins { left: 0; top: 266px; width: 850px; text-align: center; font-family: var(--head); font-size: 23px; color: var(--navy); letter-spacing: .5px; }
  .benefits { left: 36px; top: 302px; width: 778px; display: grid; grid-template-columns: repeat(4, 1fr); gap: 14px; }
  .benefit { height: 82px; border: 2px solid var(--blue-pale); border-radius: 6px; background: var(--blue-mist); padding: 8px 8px; display: flex; flex-direction: column; align-items: center; text-align: center; }
  .benefit-title { font-weight: 900; font-size: 12px; color: var(--navy); text-transform: uppercase; line-height: 1.05; }
  .benefit-body { display: flex; align-items: center; gap: 6px; margin-top: 6px; }
  .benefit-body svg { flex: none; }
  .benefit-text { font-size: 11px; line-height: 1.15; color: var(--ink); text-align: left; }
  .slogan { left: 0; top: 396px; width: 850px; text-align: center; font-weight: 900; font-size: 16px; color: var(--navy); letter-spacing: .3px; }
  .slogan .hot { color: var(--red); }

  .contact-bar { left: 0; width: 850px; height: 56px; background: var(--navy); display: flex; align-items: center; padding: 0 28px; color: var(--white); }
  .card--front .contact-bar { top: 424px; }
  .card--back .contact-bar { top: 484px; }
  .contact-bar .cta { font-weight: 900; font-size: 18px; color: var(--yellow); text-transform: uppercase; }
  .contact-bar .details { margin-left: auto; display: flex; gap: 34px; font-weight: 700; font-size: 18px; }

  /* ---------- BACK ---------- */
  .money-photo { left: 300px; top: 0; width: 550px; height: 208px;
    background: linear-gradient(120deg, #c9d3c1 0%, #9fb29b 40%, #cfe3e2 62%, #d9dccb 75%, #8da08b 100%);
    clip-path: polygon(14% 0, 100% 0, 100% 100%, 0 100%); }
  .refer-panel { left: 0; top: 0; width: 400px; height: 208px; background: var(--navy);
    clip-path: polygon(0 0, 100% 0, 80% 100%, 0 100%); }
  .refer-head { left: 30px; top: 22px; width: 300px; font-family: var(--head); text-transform: uppercase; line-height: 1; }
  .refer-head .small { display: block; font-size: 28px; color: var(--white); }
  .refer-head .big { display: block; font-size: 40px; color: var(--yellow); margin-bottom: 6px; }

  .how-band { left: 0; top: 216px; width: 850px; height: 40px; background: var(--blue-mist); }
  .how-tag { left: 0; top: 216px; width: 300px; height: 40px; background: var(--yellow); color: var(--navy);
    font-family: var(--head); font-size: 26px; line-height: 40px; padding-left: 34px;
    clip-path: polygon(0 0, 100% 0, 92% 100%, 0 100%); }

  .steps { left: 30px; top: 268px; width: 790px; display: grid; grid-template-columns: repeat(3, 1fr); gap: 20px; }
  .step { display: flex; flex-direction: column; align-items: center; text-align: center; }
  .step-photo { width: 100%; height: 118px; border: 3px solid var(--blue-pale); border-radius: 4px; }
  .step-photo--pipe { background: linear-gradient(160deg, #e9edf0, #b9c4cc 60%, #7c8d99); }
  .step-photo--roof { background: linear-gradient(180deg, #8fb6df 0%, #5a88b8 50%, #d7d7d2 100%); }
  .step-photo--sign { background: linear-gradient(180deg, #76b7ea 0%, #a7d3f3 60%, #e8c640 100%); }
  .step-title { margin-top: 10px; font-weight: 900; font-size: 15px; color: var(--navy); text-transform: uppercase; line-height: 1.1; }
  .step-text { margin-top: 4px; font-size: 13px; color: var(--ink); line-height: 1.2; }
</style>
</head>
<body>

<!-- FRONT -->
<section class="card card--front" aria-label="Flyer front">
  <div class="abs hero-photo" role="img" aria-label="Photo of blue air movers drying a flooded room"></div>
  <div class="abs hero-panel"></div>
  <h1 class="abs headline">
    <span class="line earn">Earn</span>
    <span class="line unlimited">Unlimited</span>
    <span class="line cash">Cash</span>
  </h1>
  <div class="abs hero-tag">GET PAID TO REFER A FLOOD</div>

  <div class="abs offer">
    <div class="offer-chip"><strong>$500</strong><span>Minimum</span></div>
    <div class="offer-or">OR</div>
    <div class="offer-chip"><strong>10%</strong><span>Per<br>Referral</span></div>
  </div>

  <div class="abs premier">
    <div class="premier-pill premier-pill--partner">PARTNER</div>
    <div class="premier-pill premier-pill--program">PROGRAM</div>
    <svg class="premier-badge" viewBox="0 0 58 58" aria-hidden="true">
      <circle cx="29" cy="29" r="27" fill="#ffffff" stroke="#0b2f63" stroke-width="4"/>
      <circle cx="29" cy="29" r="19" fill="#0054AA"/>
      <path d="M20 30 l6 6 l12 -13" fill="none" stroke="#ffffff" stroke-width="5" stroke-linecap="round" stroke-linejoin="round"/>
    </svg>
    <div class="premier-label">PREMIER</div>
  </div>

  <h2 class="abs wins">PARTNER WITH US &amp; EVERYBODY WINS!</h2>

  <div class="abs benefits">
    <div class="benefit">
      <div class="benefit-title">Guaranteed<br>Payout</div>
      <div class="benefit-body">
        <svg width="26" height="26" viewBox="0 0 26 26" aria-hidden="true"><circle cx="13" cy="13" r="12" fill="#F7C600"/><text x="13" y="18" text-anchor="middle" font-family="Arial" font-weight="900" font-size="14" fill="#0b2f63">$</text></svg>
        <div class="benefit-text">Minimum $500 or 10% of Total Invoice Paid Out</div>
      </div>
    </div>
    <div class="benefit">
      <div class="benefit-title">Free<br>Estimates</div>
      <div class="benefit-body">
        <svg width="26" height="26" viewBox="0 0 26 26" aria-hidden="true"><rect x="4" y="2" width="18" height="22" rx="2" fill="#0054AA"/><path d="M8 9h10M8 13h10M8 17h6" stroke="#fff" stroke-width="2"/></svg>
        <div class="benefit-text">Fast &amp; Free Inspections &amp; Written Estimates</div>
      </div>
    </div>
    <div class="benefit">
      <div class="benefit-title">Affordable<br>Solutions</div>
      <div class="benefit-body">
        <svg width="26" height="26" viewBox="0 0 26 26" aria-hidden="true"><path d="M3 13 L13 3 L23 3 L23 13 L13 23 Z" fill="#0677BA"/><circle cx="18" cy="8" r="2.5" fill="#fff"/></svg>
        <div class="benefit-text">Lowest Out of Pocket Costs for Your Customers</div>
      </div>
    </div>
    <div class="benefit">
      <div class="benefit-title">Industry<br>Leaders</div>
      <div class="benefit-body">
        <svg width="26" height="26" viewBox="0 0 26 26" aria-hidden="true"><path d="M13 2 L16 9 L24 10 L18 15 L20 23 L13 19 L6 23 L8 15 L2 10 L10 9 Z" fill="#F7C600" stroke="#0b2f63" stroke-width="1.2"/></svg>
        <div class="benefit-text">Licensed &amp; Certified Experts Provide Lasting Solutions</div>
      </div>
    </div>
  </div>

  <p class="abs slogan"><span class="hot">SEND REFERRALS.</span> GET PAID. <span class="hot">GROW YOUR BUSINESS.</span></p>

  <div class="abs contact-bar">
    <span class="cta">Call, Text or Book Online</span>
    <span class="details"><span>858-471-6093</span><span>www.BrightlaneRenovate.com</span></span>
  </div>
</section>

<!-- BACK -->
<section class="card card--back" aria-label="Flyer back">
  <div class="abs money-photo" role="img" aria-label="Photo of spread hundred-dollar bills with letter tiles spelling cash flow"></div>
  <div class="abs refer-panel"></div>
  <h2 class="abs refer-head">
    <span class="small">The More You</span>
    <span class="big">Refer</span>
    <span class="small">The More You</span>
    <span class="big">Earn</span>
  </h2>

  <div class="abs how-band"></div>
  <h3 class="abs how-tag">HOW IT WORKS</h3>

  <div class="abs steps">
    <div class="step">
      <div class="step-photo step-photo--pipe" role="img" aria-label="Photo of a leaking pipe under a sink"></div>
      <div class="step-title">Refer Flood, Mold &amp;<br>Construction Jobs</div>
      <div class="step-text">It's Simple to Refer 24/7.<br>Call, Text or Book Online</div>
    </div>
    <div class="step">
      <div class="step-photo step-photo--roof" role="img" aria-label="Photo of a restored home exterior"></div>
      <div class="step-title">We Take Care of<br>Everything</div>
      <div class="step-text">We Schedule a Free Estimate.<br>If Approved, You Get Paid.</div>
    </div>
    <div class="step">
      <div class="step-photo step-photo--sign" role="img" aria-label="Photo of a yellow road sign reading get paid to share"></div>
      <div class="step-title">Everybody Benefits<br>From Referrals</div>
      <div class="step-text">We Provide Expert Quality<br>Work for Affordable Price</div>
    </div>
  </div>

  <div class="abs contact-bar">
    <span class="cta">Call, Text or Book Online</span>
    <span class="details"><span>858-471-6093</span><span>www.BrightlaneRenovate.com</span></span>
  </div>
</section>

</body>
</html>
```